TA BRAMLEY BUSINESS CARD DESIGN PROJECT

We need to utilize our logo that was expertly created on PixelHarbor and now need to match this with a business card design.

```html
<!DOCTYPE html>
<html lang="en">
<head>
<meta charset="utf-8">
<title>TA Bramley Business Card</title>
<link rel="stylesheet" href="https://fonts.googleapis.com/css2?family=Montserrat:wght@400;500;700;800&display=swap">
<style>
  :root {
    --brand-blue: #1357a9;
    --card-white: #ffffff;
    --ink-dark: #2b2b2b;
    --backdrop: #e9ebee;
  }
  * { box-sizing: border-box; margin: 0; padding: 0; }
  html, body {
    width: 1200px; height: 900px; overflow: hidden;
    background: var(--backdrop);
    font-family: "Montserrat", sans-serif;
  }
  .sheet {
    position: relative; width: 1200px; height: 900px;
    display: flex; flex-direction: column; align-items: center; justify-content: center; gap: 40px;
  }
  .card {
    position: relative; width: 700px; height: 390px;
    border-radius: 22px; overflow: hidden;
    box-shadow: 0 10px 30px rgba(0,0,0,0.18);
  }
  /* Front */
  .card-front { background: var(--brand-blue); display: flex; align-items: center; justify-content: center; }
  .wordmark {
    display: flex; align-items: center; gap: 18px;
    color: var(--card-white); font-weight: 800; font-size: 58px; letter-spacing: 10px;
  }
  .wordmark-square { width: 34px; height: 34px; background: currentColor; flex: none; }
  /* Back */
  .card-back { background: var(--card-white); }
  .card-back .wordmark {
    position: absolute; left: 48px; top: 132px;
    color: var(--brand-blue); font-size: 30px; letter-spacing: 5px; gap: 12px;
  }
  .card-back .wordmark-square { width: 20px; height: 20px; }
  .divider {
    position: absolute; left: 372px; top: 52px; width: 2px; height: 156px; background: var(--brand-blue);
  }
  .contact { position: absolute; left: 396px; top: 34px; color: var(--ink-dark); }
  .contact-name { color: var(--brand-blue); font-weight: 800; font-size: 22px; letter-spacing: 0.5px; line-height: 1.2; }
  .contact-role { font-size: 14px; font-weight: 500; margin-top: 2px; }
  .contact-lines { list-style: none; margin-top: 12px; font-size: 14px; line-height: 1.5; }
  .contact-lines li { display: flex; align-items: center; gap: 8px; }
  .contact-lines svg { width: 13px; height: 13px; fill: var(--brand-blue); flex: none; }
  .contact-address { margin-top: 10px; font-size: 14px; line-height: 1.4; }
  .wave { position: absolute; left: 0; top: 0; width: 700px; height: 390px; }
  .website {
    position: absolute; right: 34px; bottom: 100px; color: var(--card-white);
    font-size: 15px; font-weight: 500; letter-spacing: 0.5px;
    transform: rotate(-14deg); transform-origin: right bottom;
  }
</style>
</head>
<body>
<main class="sheet">
  <section class="card card-front" aria-label="Card front">
    <div class="wordmark"><span class="wordmark-square"></span>TA BRAMLEY</div>
  </section>

  <section class="card card-back" aria-label="Card back">
    <svg class="wave" viewBox="0 0 700 390" aria-hidden="true">
      <path d="M0 390 L0 374 C220 364 330 332 440 282 C540 236 620 226 700 224 L700 390 Z" fill="var(--brand-blue)"/>
      <path d="M0 362 C220 352 330 320 440 270 C540 224 620 214 700 212" fill="none" stroke="var(--brand-blue)" stroke-width="2.5"/>
    </svg>

    <div class="wordmark"><span class="wordmark-square"></span>TA BRAMLEY</div>
    <div class="divider"></div>

    <div class="contact">
      <p class="contact-name">DANIEL REEVE</p>
      <p class="contact-role">Managing Director</p>
      <ul class="contact-lines">
        <li><svg viewBox="0 0 16 16"><path d="M3 1h3l1.5 4-2 1.3a9 9 0 0 0 4.2 4.2L11 8.5l4 1.5v3a2 2 0 0 1-2 2A12 12 0 0 1 1 3a2 2 0 0 1 2-2z"/></svg>123 456 789</li>
        <li><svg viewBox="0 0 16 16"><path d="M4 1h6l2 2v3h2v9H2V6h2zM5 2v4h6V3.5L9.5 2zM4 9v1h2V9zm3 0v1h2V9zm3 0v1h2V9zM4 11v1h2v-1zm3 0v1h2v-1zm3 0v1h2v-1z"/></svg>123 456 789</li>
        <li><svg viewBox="0 0 16 16"><path d="M1 3h14v1L8 9 1 4zM1 6l7 5 7-5v7H1z"/></svg>info@yourmail.com</li>
      </ul>
      <p class="contact-address">Your address, City<br>State, Zip 1234</p>
    </div>

    <p class="website">www.yourwebsite.com</p>
  </section>
</main>
</body>
</html>
```